I need a business card design for a new business based in South West Australia.
I specialize in residential window cleaning & general handyman maintenance.

Dale Marsh - 412 SILVER HAWK DETAILING
- Window Cleaning
- House Maintenance

```html
<!DOCTYPE html>
<html lang="en">
<head>
<meta charset="utf-8">
<title>412 Silver Hawk Detailing – Business Card</title>
<link rel="stylesheet" href="https://fonts.googleapis.com/css2?family=Old+Standard+TT:wght@400;700&display=swap">
<style>
  :root {
    --backdrop: #d9d6d0;
    --card-blue: #1f5fa0;
    --card-blue-dark: #154a82;
    --panel-light: #f4f5f7;
    --panel-grey: #dfe2e6;
    --stripe-black: #111111;
    --ink: #0d0d0d;
    --ink-soft: #222222;
    --on-blue: #ffffff;
  }
  * { margin: 0; padding: 0; box-sizing: border-box; }
  html, body { width: 1200px; height: 892px; overflow: hidden; }
  body {
    background: var(--backdrop);
    display: flex; align-items: center; justify-content: center;
    font-family: "Old Standard TT", "Times New Roman", serif;
  }
  .business-card {
    position: relative;
    width: 900px; height: 514px;
    border-radius: 4px;
    overflow: hidden;
    box-shadow: 0 10px 30px rgba(0,0,0,.25);
  }
  .card-art { position: absolute; inset: 0; width: 100%; height: 100%; }
  .identity {
    position: absolute; left: 40px; top: 48px; width: 560px;
    text-align: center; color: var(--ink);
  }
  .company-name {
    font-weight: 700; font-size: 42px; letter-spacing: .5px; line-height: 1.1;
  }
  .tagline {
    font-weight: 700; font-size: 24px; line-height: 1.15; color: var(--ink-soft);
    margin-top: 10px;
  }
  .owner-name {
    font-weight: 700; font-size: 60px; line-height: 1; margin-top: 24px;
  }
  .services {
    position: absolute; left: 560px; top: 350px;
    list-style: none; color: var(--on-blue);
    font-size: 30px; line-height: 1.25;
  }
  .services li:nth-child(2) { padding-left: 30px; }
</style>
</head>
<body>
  <article class="business-card">
    <svg class="card-art" viewBox="0 0 900 514" preserveAspectRatio="none" aria-hidden="false">
      <defs>
        <linearGradient id="blueField" x1="0" y1="0" x2="1" y2="1">
          <stop offset="0" stop-color="var(--card-blue-dark)"/>
          <stop offset="1" stop-color="var(--card-blue)"/>
        </linearGradient>
        <linearGradient id="lightPanel" x1="0" y1="0" x2="1" y2="1">
          <stop offset="0" stop-color="var(--panel-grey)"/>
          <stop offset=".5" stop-color="var(--panel-light)"/>
          <stop offset="1" stop-color="var(--panel-grey)"/>
        </linearGradient>
      </defs>
      <rect class="blue-field" width="900" height="514" fill="url(#blueField)"/>
      <path class="outer-stripe" d="M0,0 H715 Q640,360 0,500 Z" fill="#ffffff"/>
      <path class="black-stripe" d="M0,0 H700 Q620,350 0,488 Z" fill="var(--stripe-black)"/>
      <path class="inner-stripe" d="M0,0 H686 Q602,340 0,478 Z" fill="#ffffff"/>
      <path class="light-panel" d="M0,0 H670 Q585,330 0,466 Z" fill="url(#lightPanel)"
            role="img" aria-label="Faint grid backdrop with window-cleaner figures"/>
    </svg>
    <header class="identity">
      <h1 class="company-name">412 SILVER HAWK DETAILING</h1>
      <p class="tagline">residential window cleaning &amp;<br>general handyman maintenance</p>
      <p class="owner-name">Dale Marsh</p>
    </header>
    <ul class="services">
      <li>House Maintenance</li>
      <li>Window Cleaning</li>
    </ul>
  </article>
</body>
</html>
```